New Business Card Design Project

I'd like a business card design around the same modern style that I used on my website www.brovanhs.com
It's gonna be one of those round corners double-sided business cards with maybe a big logo on the front and all the info on the back of the card.

Contact Information for Business Card

Marco Delgado
425-317-6084
www.brovanhs.com

www.facebook.com/BrovanHomeServices
www.intsgram.com/BrovanHomeServices

Requirements
Must have
• it needs to look elegant and modern

```html
<!DOCTYPE html>
<html lang="en">
<head>
<meta charset="utf-8">
<title>Brovan Home Services – Business Card</title>
<link rel="stylesheet" href="https://fonts.googleapis.com/css2?family=Montserrat:wght@500;600;700&display=swap">
<style>
  :root {
    --bg: #e6e8eb;
    --card-white: #ffffff;
    --card-dark: #262628;
    --brand-blue: #1a8fd6;
    --ink: #222326;
    --ink-soft: #3a3b3f;
    --swoosh-dark: #1d1d1f;
  }
  * { box-sizing: border-box; margin: 0; padding: 0; }
  html, body { width: 1200px; height: 900px; overflow: hidden; }
  body {
    background: var(--bg);
    font-family: "Montserrat", sans-serif;
    display: flex;
    flex-direction: column;
    align-items: center;
    justify-content: center;
    gap: 44px;
  }
  .card {
    position: relative;
    width: 700px;
    height: 400px;
    border-radius: 18px;
    overflow: hidden;
    box-shadow: 0 10px 28px rgba(0,0,0,0.18);
  }
  .card--front { background: var(--card-white); }
  .card--back {
    background: var(--card-dark);
    display: flex;
    align-items: center;
    justify-content: center;
    width: 420px;
    height: 240px;
    border-radius: 12px;
  }
  .swoosh { position: absolute; left: 0; bottom: 0; width: 700px; height: 400px; }
  .brand-name {
    position: absolute;
    left: 48px;
    top: 42px;
    font-size: 34px;
    font-weight: 700;
    color: var(--brand-blue);
    letter-spacing: -0.5px;
  }
  .card--back .brand-name {
    position: static;
    font-size: 30px;
  }
  .divider {
    position: absolute;
    left: 48px;
    right: 48px;
    top: 118px;
    height: 2px;
    background: var(--brand-blue);
  }
  .contact-list {
    position: absolute;
    left: 48px;
    top: 140px;
    list-style: none;
    font-size: 14px;
    font-weight: 500;
    color: var(--ink-soft);
    line-height: 23px;
  }
  .contact-list li { display: flex; align-items: center; gap: 9px; }
  .contact-list svg { width: 12px; height: 12px; flex: none; }
  .person {
    position: absolute;
    right: 48px;
    top: 140px;
    text-align: right;
  }
  .person-name {
    font-size: 28px;
    font-weight: 600;
    color: var(--brand-blue);
    letter-spacing: 1px;
    text-transform: uppercase;
  }
  .person-title {
    font-size: 16px;
    font-weight: 500;
    color: var(--ink);
    margin-top: 2px;
  }
  .address {
    position: absolute;
    right: 48px;
    top: 232px;
    text-align: right;
    font-size: 15px;
    font-weight: 500;
    color: var(--ink);
    line-height: 23px;
  }
</style>
</head>
<body>
  <section class="card card--front">
    <svg class="swoosh" viewBox="0 0 700 400" aria-hidden="true">
      <path d="M0 322 C 190 360, 360 352, 470 400 L 0 400 Z" fill="var(--brand-blue)"/>
      <path d="M0 312 C 190 346, 370 338, 488 400" fill="none" stroke="var(--swoosh-dark)" stroke-width="5"/>
    </svg>
    <div class="brand-name">Brovan Home Services</div>
    <div class="divider"></div>
    <ul class="contact-list">
      <li><svg viewBox="0 0 12 12"><path d="M2.5 1 L4.5 1 L5.2 3.6 L4 4.6 C4.6 6 5.9 7.4 7.4 8 L8.4 6.8 L11 7.5 L11 9.5 C11 10.3 10.3 11 9.5 11 C5 10.7 1.3 7 1 2.5 C1 1.7 1.7 1 2.5 1 Z" fill="var(--ink)"/></svg>425-317-6084</li>
      <li><svg viewBox="0 0 12 12"><rect x="1" y="2.5" width="10" height="7" fill="none" stroke="var(--ink)" stroke-width="1.3"/><path d="M1 2.5 L6 6.5 L11 2.5" fill="none" stroke="var(--ink)" stroke-width="1.3"/></svg>info@brovanhs.com</li>
      <li><svg viewBox="0 0 12 12"><circle cx="6" cy="6" r="5" fill="none" stroke="var(--ink)" stroke-width="1.2"/><ellipse cx="6" cy="6" rx="2.2" ry="5" fill="none" stroke="var(--ink)" stroke-width="1"/><path d="M1 6 H11" stroke="var(--ink)" stroke-width="1"/></svg>www.brovanhs.com</li>
      <li><svg viewBox="0 0 12 12"><circle cx="6" cy="6" r="5" fill="var(--ink)"/></svg>/BrovanHomeServices</li>
      <li><svg viewBox="0 0 12 12"><rect x="1" y="1" width="10" height="10" rx="2" fill="var(--ink)"/></svg>/BrovanHomeServices</li>
    </ul>
    <div class="person">
      <div class="person-name">Marco Delgado</div>
      <div class="person-title">Director</div>
    </div>
    <div class="address">
      2741 Harlow Creek Road<br>
      Oklahoma City, OK 73012
    </div>
  </section>

  <section class="card card--back">
    <div class="brand-name">Brovan Home Services</div>
  </section>
</body>
</html>
```